Field Anchor - Design a new page for our website

The designer is to use our existing website to match color and style and the documents provided to create a webpage that reflects the information in the brochure attached. This should also include a button to download our brochure and a form to request more information by entering name, phone, and email. This page will be added to our main site and will be coded by our webmaster team.

View website at www.harrowfield.us

The successful designer will be asked to also design another page for additional compensation.

Target Market(s)

Security and Law Enforcement

Industry/Entity Type

Security Service

Coding

Number of Pages Required

1 page

Font styles to use
Other font styles liked:
• Raleway or match site font and style

Requirements
Must have
• Match in color and style to our existing site as this page will be added to the existing website.

UPDATE: Place FRB Logo (attached to the brief) in a horizontal bar the width of the page with the following text:

"Field Anchor and all of Harrowfield's services are available on under our FRB Contract." (Add button) Click for Info
Nice to have
• Simple design expressing clean and easy to comprehend points

Please be creative, use the ability to scroll vertically on the page to space out the content and add supporting graphics or images.

```html
<!DOCTYPE html>
<html lang="en">
<head>
<meta charset="utf-8">
<title>Harrowfield Consulting</title>
<link href="https://fonts.googleapis.com/css2?family=Raleway:wght@400;500;600;700;800&family=Open+Sans:wght@400;600&display=swap" rel="stylesheet">
<style>
:root{
  --blue:#1f64b4;
  --blue-bright:#2b8fe0;
  --navy:#123a6e;
  --navy-deep:#0b2a55;
  --ink:#1c1f24;
  --text:#3c3f44;
  --muted:#6b7079;
  --line:#d9dde3;
  --white:#ffffff;
  --footer:#1d1f23;
  --footer-bar:#141518;
}
*{box-sizing:border-box;margin:0;padding:0}
html,body{width:1200px;height:4464px;overflow:hidden;background:var(--white)}
body{font-family:"Open Sans",Arial,sans-serif;color:var(--text);position:relative}
h1,h2,h3,.nav,.btn{font-family:"Raleway",Arial,sans-serif}
section,header,footer{position:absolute;left:0;width:1200px}

/* header */
.site-header{top:0;height:110px;background:var(--white);box-shadow:0 2px 6px rgba(0,0,0,.08);z-index:3}
.brand{position:absolute;left:48px;top:28px;display:flex;align-items:center;gap:12px;font-family:"Raleway",sans-serif;font-weight:800;font-size:34px;color:var(--ink);letter-spacing:.5px}
.brand-mark{width:34px;height:34px;border-radius:50%;background:var(--blue)}
.nav{position:absolute;right:40px;top:40px;display:flex;gap:36px;font-size:18px;font-weight:500;color:var(--ink)}
.nav a{color:inherit;text-decoration:none;padding-bottom:8px}
.nav a.active{color:var(--blue);border-bottom:2px solid var(--blue)}

/* hero */
.hero{top:110px;height:780px;overflow:hidden}
.hero-photo{position:absolute;inset:0;background:linear-gradient(160deg,#c9d3dc 0%,#8f9aa6 40%,#5a5f66 75%,#3a3c40 100%)}
.hero-title{position:absolute;left:0;right:0;top:260px;text-align:center;color:var(--white);font-family:"Raleway",sans-serif;font-weight:700;text-transform:uppercase;text-shadow:0 2px 8px rgba(0,0,0,.45)}
.hero-title .l1{font-size:48px;letter-spacing:1px;background:rgba(20,60,110,.35);display:inline-block;padding:4px 14px}
.hero-title .l2{font-size:40px;margin-top:4px}
.hero-dots{position:absolute;left:0;right:0;top:570px;text-align:center}
.hero-dots span{display:inline-block;width:10px;height:10px;border-radius:50%;background:rgba(255,255,255,.6);margin:0 5px}
.hero-dots span.on{background:var(--white)}
.hero-shape{position:absolute;left:0;bottom:0}

/* about */
.about{top:890px;height:370px;text-align:center}
.section-title{font-family:"Raleway",sans-serif;font-weight:700;font-size:42px;color:var(--ink);text-transform:uppercase;letter-spacing:.5px}
.section-title .hl{color:var(--blue-bright)}
.about .section-title{margin-top:100px}
.about p{width:800px;margin:38px auto 0;font-size:18px;line-height:32px;color:var(--text)}

/* technologies */
.technologies{top:1260px;height:660px;background:linear-gradient(180deg,var(--navy-deep),var(--blue) 55%,var(--navy));color:var(--white);text-align:center}
.technologies .section-title{color:var(--white);margin-top:62px}
.tech-rule{width:90px;height:3px;background:var(--white);margin:16px auto 0}
.tech-grid{position:absolute;left:170px;top:180px;width:860px;display:grid;grid-template-columns:repeat(3,1fr);row-gap:70px}
.tech-item{display:flex;flex-direction:column;align-items:center}
.tech-icon{width:86px;height:86px;border-radius:50%;background:var(--white);display:flex;align-items:center;justify-content:center}
.tech-item h3{margin-top:22px;font-size:15px;font-weight:700;text-transform:uppercase;line-height:22px;letter-spacing:.3px}

/* communication */
.communication{top:1920px;height:760px;text-align:center}
.communication .section-title{margin-top:112px}
.comm-cards{position:absolute;left:110px;top:210px;display:flex;gap:36px}
.comm-card{width:300px;height:410px;background:var(--white);box-shadow:0 4px 14px rgba(0,0,0,.18)}
.comm-photo{height:210px}
.comm-card h3{margin:22px 20px 0;font-size:17px;font-weight:700;color:var(--blue);text-transform:uppercase;line-height:24px}
.comm-card p{margin:14px 26px 0;font-size:13px;line-height:20px;color:var(--muted)}

/* events */
.events{top:2770px;height:450px;background:linear-gradient(90deg,var(--navy-deep),var(--blue));color:var(--white)}
.events-photo{position:absolute;left:0;top:0;width:500px;height:450px;background:linear-gradient(135deg,#5b6670,#2f3b47 60%,#1b2a3d)}
.events-body{position:absolute;left:520px;top:52px;width:620px}
.events-body h2{font-size:40px;font-weight:600;text-transform:uppercase}
.events-body h3{font-size:22px;font-weight:600;text-transform:uppercase;margin-top:8px}
.events-body p{font-size:14px;line-height:24px;margin-top:22px}
.btn{display:inline-block;margin-top:24px;background:var(--white);color:var(--navy);font-weight:700;font-size:14px;text-transform:uppercase;padding:12px 26px;border-radius:26px;text-decoration:none}

/* support */
.support{top:3220px;height:600px}
.support .section-title{text-align:center;margin-top:88px}
.support-list{position:absolute;left:110px;top:210px;width:600px}
.support-item{margin-bottom:40px}
.support-item h3{display:flex;align-items:center;gap:14px;font-size:17px;font-weight:700;color:var(--blue);text-transform:uppercase}
.support-item p{font-size:15px;line-height:26px;margin-top:14px}
.support-photo{position:absolute;left:750px;top:160px;width:340px;height:360px;background:linear-gradient(180deg,#dfe3e8,#b8c0c8 55%,#8b939c)}

/* footer */
.footer-shape{top:3780px;height:200px}
.site-footer{top:3980px;height:440px;background:var(--footer);color:#e6e8eb}
.footer-col h3{font-size:18px;font-weight:700;text-transform:uppercase;letter-spacing:.5px}
.contact{position:absolute;left:110px;top:40px}
.contact ul{list-style:none;margin-top:30px}
.contact li{display:flex;gap:20px;align-items:flex-start;font-size:14px;line-height:22px;margin-bottom:28px}
.footer-brand{position:absolute;left:440px;top:40px;width:320px;text-align:center}
.footer-brand .brand-name{display:inline-flex;align-items:center;gap:10px;font-family:"Raleway",sans-serif;font-weight:800;font-size:32px;color:#e6e8eb}
.footer-brand .brand-mark{width:30px;height:30px;border-radius:50%;background:#e6e8eb}
.socials{margin-top:34px;display:flex;justify-content:center;gap:18px}
.socials span{width:36px;height:36px;border-radius:50%;border:2px solid #e6e8eb}
.touch{position:absolute;left:810px;top:40px;width:270px}
.touch form{margin-top:20px}
.touch input{display:block;width:270px;height:40px;margin-bottom:14px;border:none;padding:0 12px;font-size:14px;font-family:"Open Sans",sans-serif}
.touch button{width:100px;height:40px;background:var(--blue);color:var(--white);border:none;border-radius:20px;font-family:"Raleway",sans-serif;font-weight:700;font-size:15px}
.copyright{top:4420px;height:44px;background:var(--footer-bar);color:#9ca1a8;font-size:12px;text-align:center;line-height:44px}
</style>
</head>
<body>

<header class="site-header">
  <div class="brand"><span class="brand-mark"></span>Harrowfield</div>
  <nav class="nav">
    <a class="active" href="#">Home</a><a href="#">About Us</a><a href="#">Our Team</a><a href="#">Careers</a><a href="#">Core Markets</a><a href="#">Blog</a><a href="#">Contact Us</a>
  </nav>
</header>

<section class="hero">
  <div class="hero-photo" role="img" aria-label="Three women walking with shopping bags through a bright mall"></div>
  <div class="hero-title">
    <div class="l1">Creating Secure Environment</div>
    <div class="l2">So You Can Be Carefree</div>
  </div>
  <div class="hero-dots"><span class="on"></span><span></span><span></span></div>
  <svg class="hero-shape" width="1200" height="260" viewBox="0 0 1200 260">
    <polygon points="0,260 0,150 600,230 1200,120 1200,260" fill="#ffffff"/>
    <polygon points="0,150 0,110 600,230" fill="#123a6e"/>
    <polygon points="320,190 600,230 880,178 600,255" fill="#0b2a55"/>
    <polygon points="600,230 1200,80 1200,120" fill="#1f64b4"/>
  </svg>
</section>

<section class="about">
  <h2 class="section-title">About <span class="hl">Harrowfield Consulting</span></h2>
  <p>Harrowfield Consulting is a team of seasoned security professionals with backgrounds in security management, law enforcement, emergency services and security technology. Put our expertise and experience to work for you!</p>
</section>

<section class="technologies">
  <h2 class="section-title">Security Technologies</h2>
  <div class="tech-rule"></div>
  <div class="tech-grid">
    <div class="tech-item">
      <div class="tech-icon"><svg width="46" height="46" viewBox="0 0 46 46" fill="none" stroke="#123a6e" stroke-width="2.5"><rect x="6" y="12" width="34" height="24" rx="3"/><circle cx="23" cy="24" r="7"/></svg></div>
      <h3>Rapid Video System<br>Deployment</h3>
    </div>
    <div class="tech-item">
      <div class="tech-icon"><svg width="46" height="46" viewBox="0 0 46 46" fill="none" stroke="#123a6e" stroke-width="2.5"><line x1="23" y1="8" x2="23" y2="38"/><line x1="10" y1="16" x2="36" y2="16"/><circle cx="10" cy="16" r="4"/><circle cx="36" cy="16" r="4"/></svg></div>
      <h3>Aerial Drone<br>Surveillance</h3>
    </div>
    <div class="tech-item">
      <div class="tech-icon"><svg width="46" height="46" viewBox="0 0 46 46" fill="none" stroke="#123a6e" stroke-width="2.5"><path d="M10 36 L23 10 L36 36"/><path d="M14 20 a14 14 0 0 1 18 0"/></svg></div>
      <h3>Drone Detection<br>Technology</h3>
    </div>
    <div class="tech-item">
      <div class="tech-icon"><svg width="46" height="46" viewBox="0 0 46 46" fill="none" stroke="#123a6e" stroke-width="2.5"><circle cx="23" cy="23" r="14"/><circle cx="23" cy="23" r="5"/></svg></div>
      <h3>Gunfire Detection</h3>
    </div>
    <div class="tech-item">
      <div class="tech-icon"><svg width="46" height="46" viewBox="0 0 46 46" fill="none" stroke="#123a6e" stroke-width="2.5"><path d="M10 32 h26 a7 7 0 0 0 -4 -13 a9 9 0 0 0 -17 3 a5 5 0 0 0 -5 10z"/></svg></div>
      <h3>Real-Time Weather<br>Monitoring</h3>
    </div>
    <div class="tech-item">
      <div class="tech-icon"><svg width="46" height="46" viewBox="0 0 46 46" fill="none" stroke="#123a6e" stroke-width="2.5"><rect x="8" y="10" width="30" height="22" rx="2"/><line x1="16" y1="38" x2="30" y2="38"/><line x1="14" y1="18" x2="32" y2="18"/><line x1="14" y1="24" x2="26" y2="24"/></svg></div>
      <h3>Social Media<br>Monitoring</h3>
    </div>
  </div>
</section>

<section class="communication">
  <h2 class="section-title"><span class="hl" style="color:var(--blue)">Communication</span> Systems</h2>
  <div class="comm-cards">
    <article class="comm-card">
      <div class="comm-photo" role="img" aria-label="Operator wearing a headset at a call desk" style="background:linear-gradient(135deg,#e4e8ec,#a9b2bb)"></div>
      <h3>Landline Telephone<br>Service</h3>
      <p>Crisp, clear communications with landline-based cellular or satellite service for critical public use.</p>
    </article>
    <article class="comm-card">
      <div class="comm-photo" role="img" aria-label="Man speaking into a two-way radio" style="background:linear-gradient(135deg,#cfd6dd,#6f7a86)"></div>
      <h3>Two-Way Radios and<br>Cellular PTT Radios</h3>
      <p>Our two-way radios can be programmed to our clients' operating frequencies to expand their current radio communications into the Field Anchor.</p>
    </article>
    <article class="comm-card">
      <div class="comm-photo" role="img" aria-label="Satellite orbiting above the earth" style="background:linear-gradient(135deg,#0b1a33,#1f64b4)"></div>
      <h3>Satellite TV, Radio, and<br>Cellular Data</h3>
      <p>Field Anchor ensures continuous, high-speed, reliable data communications, coupled with live satellite TV and radio to maximize access to mission information.</p>
    </article>
  </div>
</section>

<section class="events">
  <div class="events-photo" role="img" aria-label="Presenter in a suit pointing at a chart on a screen"></div>
  <div class="events-body">
    <h2>Special Events</h2>
    <h3>Pose Special Challenges</h3>
    <p>Managing security is stressful under the best of circumstances – planning for both the expected and unexpected is part of the job. But when you're tasked with securing a special event, emergency or disaster recovery, the "unexpected" takes on an additional dimension, pertaining not only to the security threats you may have to address but also to the uncertainty of security operations and infrastructure at your disposal. How do you quickly and economically set up a mobile security operations center, equipped to gather and disseminate information, coordinate personnel and manage operations and response teams?</p>
    <a class="btn" href="#">Download Brochure</a>
  </div>
</section>

<section class="support">
  <h2 class="section-title">Support <span class="hl">Services</span></h2>
  <div class="support-list">
    <div class="support-item">
      <h3><svg width="26" height="26" viewBox="0 0 26 26" fill="none" stroke="#1f64b4" stroke-width="2.5"><circle cx="13" cy="13" r="11"/><path d="M8 13 l4 4 l7 -8"/></svg>Professional Technical Staff</h3>
      <p>Our highly knowledgeable technical staff ensures that the technology aboard the Field Anchor is expressly programmed and deployed for each event to maximize its effectiveness.</p>
    </div>
    <div class="support-item">
      <h3><svg width="26" height="26" viewBox="0 0 26 26" fill="none" stroke="#1f64b4" stroke-width="2.5"><circle cx="13" cy="13" r="11"/><path d="M8 13 l4 4 l7 -8"/></svg>Seasoned Security Professionals</h3>
      <p>Don't have a professional staff to plan and operate the security of your event? Harrowfield's professional staff holds decades of experience as first responders and possess deep knowledge of special event planning, security operations and response and recovery.</p>
    </div>
  </div>
  <div class="support-photo" role="img" aria-label="Business people standing in a bright glass office"></div>
</section>

<section class="footer-shape">
  <svg width="1200" height="200" viewBox="0 0 1200 200">
    <polygon points="0,200 0,60 600,170 1200,40 1200,200" fill="#1d1f23"/>
    <polygon points="0,60 0,0 600,170" fill="#123a6e"/>
    <polygon points="600,170 1200,0 1200,40" fill="#1f64b4"/>
    <polygon points="300,115 600,170 900,105 600,200" fill="#0b2a55"/>
  </svg>
</section>

<footer class="site-footer">
  <div class="footer-col contact">
    <h3>Contact Us</h3>
    <ul>
      <li><svg width="20" height="24" viewBox="0 0 20 24" fill="#e6e8eb"><path d="M10 0a8 8 0 0 0-8 8c0 6 8 16 8 16s8-10 8-16a8 8 0 0 0-8-8zm0 11a3 3 0 1 1 0-6 3 3 0 0 1 0 6z"/></svg><span>Harrowfield Consulting<br>480 Quarry Lane, Suite 12<br>Brookhaven, New York 10990</span></li>
      <li><svg width="20" height="20" viewBox="0 0 20 20" fill="#e6e8eb"><path d="M4 1l4 4-2 3c1 2 3 4 5 5l3-2 4 4-3 3C8 18 2 12 1 4z"/></svg><span>866.555.0142</span></li>
      <li><svg width="20" height="16" viewBox="0 0 20 16" fill="none" stroke="#e6e8eb" stroke-width="2"><rect x="1" y="1" width="18" height="14"/><path d="M1 1l9 8 9-8"/></svg><span>info@harrowfield.us</span></li>
    </ul>
  </div>
  <div class="footer-brand">
    <div class="brand-name"><span class="brand-mark"></span>Harrowfield</div>
    <div class="socials"><span></span><span></span><span></span></div>
  </div>
  <div class="footer-col touch">
    <h3>Get In Touch</h3>
    <form>
      <input type="text" placeholder="Name">
      <input type="text" placeholder="Phone">
      <input type="text" placeholder="Email">
      <button type="button">Send</button>
    </form>
  </div>
</footer>

<section class="copyright">Copyright © 2020 Copyright Company Name | All Rights Reserved</section>

</body>
</html>
```